PDF flyer for our companies' two main products: Food processing machines.

PDF flyer with showcasing two products. Flyer can be one page per product, or both products on the same page.

Product #1: Labeled "Ribbon blenders".
Showing a photo of the machine, and the details/features offered with that machine. Product description must also say: "Sizes available; 2 Cu Ft. - 450 Cu Ft."

Product #2: Labeled: " Auger hoppers / Screw feeders"
Showing a photo of the machine, and the details/features offered with that machine.

SEE UPLOADED IMAGES; "Ribbon Blenders EXAMPLE FLYER".
& "Auger Hoppers / Screw Conveyors EXAMPLE FLYER" for a rough idea of what we are looking for.

Target Market(s)

Copackers, Packing houses, Food manufacturers, protein powder producers,

Industry/Entity Type

Commercial Food processing / packing / mixing equipment

Font styles to use
Serif

Colors
0054AA
0677BA
7BADD7
CADEEF
E8F1F8

Requirements
Must have
• Company logo on top of flyer.
Nice to have
• I would like for the flyer to show some stock images of common ingredients, similar to the images uploaded.
Should not have
• Pictures with background. Backgrounds must be removed from provides photos. "clipping path"

```html
<!DOCTYPE html>
<html lang="en">
<head>
<meta charset="utf-8">
<title>Harrowmere Process Co. – Product Flyer</title>
<link rel="stylesheet" href="https://fonts.googleapis.com/css2?family=Audiowide&family=Poppins:wght@400;500&family=Roboto+Condensed:wght@400;500&family=Arimo:wght@400;700&display=swap">
<style>
:root{
  --canvas:#d2dfea;
  --blue-deep:#0054aa;
  --blue:#0677ba;
  --blue-band:#1c66bf;
  --blue-soft:#7badd7;
  --blue-pale:#cadeef;
  --blue-mist:#e8f1f8;
  --panel-grey:#e1e9f1;
  --ink:#1d2433;
  --ink-line:#1b2a44;
  --white:#ffffff;
}
*{margin:0;padding:0;box-sizing:border-box}
html,body{width:1200px;height:837px;overflow:hidden;background:var(--canvas)}
body{position:relative;font-family:"Poppins",sans-serif;color:var(--ink)}
.page{position:absolute;top:78px;width:480px;height:680px;background:var(--white);overflow:hidden}
.page--blenders{left:101px}
.page--hoppers{left:619px}
.wave{position:absolute;left:0;width:480px}
.wave--top{top:0;height:130px}
.wave--bottom{top:540px;height:140px}
.brand{position:absolute;top:28px;display:flex;align-items:center;gap:6px;color:var(--white);font-family:"Audiowide",sans-serif;font-size:12px;letter-spacing:1px}
.brand-dot{width:12px;height:12px;border-radius:50%;background:var(--white)}
.page--blenders .brand{left:22px}
.page--hoppers .brand{right:22px}
.photo{position:absolute}
.photo--blender{left:250px;top:27px;width:182px;height:182px;border-radius:50%;background:radial-gradient(circle at 50% 50%,#b9bec4 0%,#dfe2e5 45%,#ececee 70%)}
.ingredient{position:absolute;border-radius:50%;box-shadow:0 1px 4px rgba(0,0,0,.2)}
.ing-a{background:radial-gradient(circle,#a8752e 30%,#f6f0e6 72%)}
.ing-b{background:radial-gradient(circle,#8c2d1a 20%,#4a2c20 70%)}
.ing-c{background:radial-gradient(circle,#6a5a48 25%,#f4f2ee 70%)}
.ing-d{background:radial-gradient(circle,#222 20%,#f4f4f4 62%)}
.ing-e{background:radial-gradient(circle,#c89a5a 28%,#f6f1ea 70%)}
.ing-f{background:radial-gradient(circle,#b6a084 28%,#f6f2ec 70%)}
.ing-g{background:radial-gradient(circle,#8a4a26 28%,#f6efe8 70%)}
.title{position:absolute;font-family:"Audiowide",sans-serif;color:var(--blue-deep);letter-spacing:.5px;font-weight:400}
.lead{position:absolute;font-size:8.2px;line-height:13px;color:var(--ink)}
.size-pill{position:absolute;left:30px;top:184px;width:116px;height:33px;border-radius:50%;background:var(--blue-deep);box-shadow:0 0 0 1.5px var(--white),0 0 0 2.5px var(--blue-deep);color:var(--white);font-family:"Audiowide",sans-serif;font-size:7.2px;line-height:10.5px;padding:6px 0 0 17px;letter-spacing:.3px}
.features-band{position:absolute;left:0;top:247px;width:480px;height:160px;display:flex}
.features-col{width:240px;height:100%;padding:27px 0 0 32px}
.features-col--standard{background:var(--panel-grey)}
.features-col--options{background:linear-gradient(135deg,#1a5fae 0%,#2a78c9 55%,#1b62b4 100%)}
.col-title{font-family:"Audiowide",sans-serif;font-size:10.5px;color:var(--blue-deep);margin-bottom:6px;letter-spacing:.3px}
.features-col--options .col-title{color:var(--white)}
.spec-list{list-style:none;font-size:5.7px;line-height:10.5px}
.spec-list li{display:flex;gap:2px}
.spec-list li::before{content:"";flex:none;width:5px;height:5px;margin-top:2.7px;border-radius:50%;background:var(--blue-deep)}
.features-col--options .spec-list{color:var(--white)}
.features-col--options .spec-list li::before{background:var(--white)}
.spec-table{position:absolute;border-collapse:collapse}
.blender-table{left:44px;top:427px;width:393px;font-family:"Arimo",sans-serif;font-size:5px;color:#111}
.blender-table td{border:0.6px solid #444;border-top:none;border-bottom:0.4px solid #bbb;height:8.95px;padding:0 1.5px;white-space:nowrap}
.blender-table tr:first-child td,.blender-table td:first-child{font-weight:700}
.blender-table tr:last-child td{border-bottom:0.6px solid #444}
.footer{position:absolute;left:0;width:480px;top:638px;text-align:center;color:var(--white);font-size:8.4px;line-height:15px}
.footer svg{width:7px;height:7px;vertical-align:-1px;margin-right:2px}
.footer .sep{margin:0 6px}
.photo--auger{left:14px;top:58px;width:207px;height:211px;background:linear-gradient(160deg,var(--blue-mist) 0%,#dfe6ec 55%,#b8bcc1 100%)}
.hopper-features{position:absolute;left:250px;top:229px}
.hopper-features .col-title{font-size:12.5px;margin-bottom:6px}
.hopper-features .spec-list{font-size:8.4px;line-height:16.2px}
.hopper-features .spec-list li{gap:3px}
.hopper-features .spec-list li::before{width:6.5px;height:6.5px;margin-top:4.8px;background:var(--ink)}
.hopper-table{left:14px;top:361px;width:446px;font-family:"Roboto Condensed",sans-serif;font-size:9px;font-weight:500;color:#111;table-layout:fixed;border:1.5px solid #111}
.hopper-table td{border:1.2px solid #111;height:13.5px;padding:0 2px;white-space:nowrap;overflow:hidden}
.hopper-table .center{text-align:center}
.hopper-table sub{font-size:5px;vertical-align:0}
.offered{position:absolute;left:43px;top:498px;width:397px}
.offered .col-title{font-size:12.5px;margin-bottom:5px}
.offered p{font-size:8.3px;line-height:13.6px;text-align:justify}
</style>
</head>
<body>

<section class="page page--blenders">
  <svg class="wave wave--top" viewBox="0 0 480 130" aria-hidden="true">
    <path d="M0 0H480V55Q230 58 0 118Z" fill="var(--blue-band)"/>
    <path d="M0 114Q230 54 480 52" fill="none" stroke="var(--ink-line)" stroke-width="1.4"/>
  </svg>
  <div class="brand"><span class="brand-dot"></span>HARROWMERE</div>

  <div class="photo photo--blender" role="img" aria-label="Photo of a stainless steel ribbon blender on a wheeled frame with control panel"></div>
  <div class="ingredient ing-a" style="left:408px;top:81px;width:36px;height:36px" role="img" aria-label="Ground spice powder"></div>
  <div class="ingredient ing-b" style="left:403px;top:134px;width:36px;height:36px" role="img" aria-label="Assorted colourful spices"></div>

  <h1 class="title" style="left:30px;top:113px;font-size:17px">RIBBON BLENDERS</h1>
  <p class="lead" style="left:30px;top:140px;width:200px">Sed ut perspiciatis unde omnis iste natus error sit voluptatem accusantium doloremque laudantium, totam rem aperiam,</p>
  <div class="size-pill">SIZES AVAILABLE<br>2 CU FT. - 450 CU FT</div>

  <div class="features-band">
    <div class="features-col features-col--standard">
      <h2 class="col-title">STANDARD FEATURES:</h2>
      <ul class="spec-list">
        <li>304 stainless steel construction.</li>
        <li>Pre-wired control panels with; batch timer, on/off switch, emergency stop button.</li>
        <li>Food grade compression shaft seals.</li>
        <li>Safety sensor on lid for automatic shutoff when opened.</li>
        <li>Air actuated discharge valve.</li>
        <li>1 piece hinged lid with safety grating.</li>
        <li>Power options; 220v/4.80v.</li>
        <li>24' standard discharge height.</li>
        <li>Castor wheels on 53cf units and smaller</li>
      </ul>
    </div>
    <div class="features-col features-col--options" role="img" aria-label="Blue-tinted workshop photo behind option list">
      <h2 class="col-title">OPTION:</h2>
      <ul class="spec-list">
        <li>Dual hinged lids available on custom orders.</li>
        <li>Knife gate style discharge available on custom orders.</li>
        <li>Air purge seals available on custom orders.</li>
        <li>316 stainless material available on custom orders.</li>
        <li>Custom height modification.</li>
        <li>Liquid spray systems</li>
        <li>(VFD) Variable Frequency Drives</li>
        <li>Leg extensions</li>
      </ul>
    </div>
  </div>

  <table class="spec-table blender-table">
    <tr><td>Model Size</td><td>5cf</td><td>7CF</td><td>10.5CF</td><td>17.5CF</td><td>35CF</td><td>53CF</td><td>70.5CF</td><td>106CF</td></tr>
    <tr><td>Working Liters</td><td>120L</td><td>200L</td><td>300L</td><td>500L</td><td>1000L</td><td>1500L</td><td>2000L</td><td>3000L</td></tr>
    <tr><td>Fill Capicty</td><td>5CF / 150L</td><td>9CF / 250L</td><td>13CF / 375L</td><td>22CF / 625L</td><td>44CF / 1250L</td><td>66CF / 1875L</td><td>88CF / 2500L</td><td>132CF / 3750L</td></tr>
    <tr><td>Weight</td><td>440lbs</td><td>550lbs</td><td>770lbs</td><td>1212lbs</td><td>1874lbs</td><td>2645lbs</td><td>3527lbs</td><td>5511lbs</td></tr>
    <tr><td>Motor Size</td><td>4hp</td><td>5.3hp</td><td>6.7hp</td><td>10hp</td><td>14.75hp</td><td>20hp</td><td>25hp</td><td>30hp</td></tr>
    <tr><td>Total Length</td><td>50"</td><td>53.5"</td><td>63"</td><td>72"</td><td>94"</td><td>102"</td><td>131.5"</td><td>157.5"</td></tr>
    <tr><td>Total Width</td><td>28"</td><td>34"</td><td>41.5"</td><td>45"</td><td>52"</td><td>66"</td><td>52.5"</td><td>54"</td></tr>
    <tr><td>Total Height</td><td>66"</td><td>69"</td><td>71"</td><td>82"</td><td>87"</td><td>95"</td><td>76"</td><td>110"</td></tr>
    <tr><td>Tub Length</td><td>31.5"</td><td>35.5"</td><td>41"</td><td>47"</td><td>59"</td><td>70"</td><td>75"</td><td>100"</td></tr>
    <tr><td>Tub Width</td><td>16.5"</td><td>22"</td><td>25"</td><td>27.5"</td><td>35.5"</td><td>39"</td><td>48"</td><td>48"</td></tr>
    <tr><td>Tub Height</td><td>20.5"</td><td>26"</td><td>28"</td><td>33"</td><td>41"</td><td>46"</td><td>51"</td><td>53"</td></tr>
    <tr><td>Shaft Diameter</td><td>2"</td><td>2-1/4"</td><td>2-5/8"</td><td>3"</td><td>3.5"</td><td>4"</td><td>4"</td><td>5-1/4"</td></tr>
    <tr><td>Tub Thickness</td><td>3mm</td><td>3mm</td><td>3mm</td><td>4mm</td><td>4mm</td><td>5mm</td><td>5mm</td><td>6mm</td></tr>
    <tr><td>Ribbon Thickness</td><td>6mm</td><td>8mm</td><td>8mm</td><td>8mm</td><td>10mm</td><td>12mm</td><td>12mm</td><td>14mm</td></tr>
    <tr><td>Max RPM</td><td>46 rpm</td><td>46 rpm</td><td>46 rpm</td><td>46 rpm</td><td>30 rpm</td><td>31 rpm</td><td>32 rpm</td><td>33 rpm</td></tr>
  </table>

  <svg class="wave wave--bottom" viewBox="0 0 480 140" aria-hidden="true">
    <path d="M0 82Q280 70 480 26V140H0Z" fill="var(--blue-band)"/>
    <path d="M0 74Q280 64 480 20" fill="none" stroke="var(--ink-line)" stroke-width="1.4"/>
  </svg>
  <div class="footer">
    <div><svg viewBox="0 0 10 10"><circle cx="5" cy="5" r="4.3" fill="none" stroke="#fff" stroke-width=".9"/><path d="M.7 5h8.6M5 .7c-2.4 2.6-2.4 6 0 8.6M5 .7c2.4 2.6 2.4 6 0 8.6" fill="none" stroke="#fff" stroke-width=".8"/></svg>www.harrowmereprocess.com</div>
    <div><svg viewBox="0 0 10 10"><path d="M2 .8l1.8 2.3-1 1.2c.6 1.3 1.6 2.3 2.9 2.9l1.2-1L9.2 8 8 9.3C4.3 9 1 5.7.7 2Z" fill="#fff"/></svg>+1 555 014 2290<span class="sep">|</span><svg viewBox="0 0 10 10"><rect x=".5" y="2" width="9" height="6.5" fill="#fff"/><path d="M.5 2.3 5 5.8l4.5-3.5" fill="none" stroke="var(--blue-band)" stroke-width=".9"/></svg>hello@harrowmereprocess.com</div>
  </div>
</section>

<section class="page page--hoppers">
  <svg class="wave wave--top" viewBox="0 0 480 130" aria-hidden="true">
    <path d="M0 0H480V118Q250 58 0 55Z" fill="var(--blue-band)"/>
    <path d="M0 52Q250 54 480 114" fill="none" stroke="var(--ink-line)" stroke-width="1.4"/>
  </svg>
  <div class="brand"><span class="brand-dot"></span>HARROWMERE</div>

  <div class="photo photo--auger" role="img" aria-label="Photo of a stainless steel auger hopper with an inclined screw feeder tube"></div>

  <div class="ingredient ing-a" style="left:242px;top:116px;width:42px;height:42px" role="img" aria-label="Ground spice powder"></div>
  <div class="ingredient ing-c" style="left:321px;top:116px;width:42px;height:42px" role="img" aria-label="Cumin seeds"></div>
  <div class="ingredient ing-d" style="left:400px;top:116px;width:42px;height:42px" role="img" aria-label="Black peppercorns"></div>
  <div class="ingredient ing-e" style="left:242px;top:170px;width:42px;height:42px" role="img" aria-label="Fresh ginger root"></div>
  <div class="ingredient ing-f" style="left:321px;top:170px;width:42px;height:42px" role="img" aria-label="Sesame seeds"></div>
  <div class="ingredient ing-g" style="left:400px;top:170px;width:42px;height:42px" role="img" aria-label="Cinnamon sticks"></div>

  <div class="hopper-features">
    <h2 class="col-title">STANDARD FEATURES:</h2>
    <ul class="spec-list">
      <li>Direct Drive</li>
      <li>304 Stainless steel construction</li>
      <li>Stainless steel safety grating</li>
      <li>Pre-wired control panel</li>
      <li>Electric Vibrator</li>
      <li>Castor Wheels.</li>
    </ul>
  </div>

  <h1 class="title" style="left:15px;top:288px;font-size:17px">AUGER HOPPERS</h1>
  <p class="lead" style="left:15px;top:314px;width:200px;font-size:8.4px">This machine is an "Auger hopper". Put on same page as "Auger Hopper features".</p>

  <table class="spec-table hopper-table">
    <colgroup><col style="width:83px"><col style="width:81px"><col style="width:55px"><col style="width:56px"><col style="width:55px"><col style="width:55px"><col style="width:61px"></colgroup>
    <tr><td>MODEL</td><td>AH-A2</td><td>AH-A3</td><td>AH-A5</td><td>AH-A7</td><td>AH-A8</td><td>AH-A12</td></tr>
    <tr><td>FEEDING RATE</td><td>2m³<sub>/Hr</sub></td><td>3m³<sub>/Hr</sub></td><td>5m³<sub>/Hr</sub></td><td>7m³<sub>/Hr</sub></td><td>8m³<sub>/Hr</sub></td><td>12m³<sub>/Hr</sub></td></tr>
    <tr><td>PIPE DIAMETER</td><td>4"</td><td>4-1/2""</td><td>5-1/2"</td><td>6-1/4"</td><td>6-1/2"</td><td>8-1/2"</td></tr>
    <tr><td>HOPPER VOL.</td><td>3.5CF</td><td class="center" colspan="5">7CF</td></tr>
    <tr><td>DIMENSIONS</td><td>28.6"x24.4"x31.5"</td><td class="center" colspan="5">40" x 32" x 35"</td></tr>
    <tr><td>TOTAL WEIGHT</td><td>221LBS</td><td>287LBS</td><td>397LBS</td><td>441LBS</td><td>485LBS</td><td>596LBS</td></tr>
    <tr><td>CHARGING HEIGHT</td><td class="center" colspan="6">STANDARD 72 INCHES. (40" - 196" AVAILABLE)</td></tr>
    <tr><td>CHARGING ANGLE</td><td class="center" colspan="6">STANDARD 45°&nbsp;&nbsp;&nbsp;&nbsp;(30°-60° AVAILABLE)</td></tr>
  </table>

  <div class="offered">
    <h2 class="col-title">MACHINE OFFERED :</h2>
    <p>Square or round hopper. 3.5cf and 7cf hoppers are standard. Custom hoppers up to 200cf. VFD (Variable Frequency Drive). Clamshell Auger tube for easy cleanout. - 316 Stainless steel construction.</p>
  </div>

  <svg class="wave wave--bottom" viewBox="0 0 480 140" aria-hidden="true">
    <path d="M0 27Q200 72 480 82V140H0Z" fill="var(--blue-band)"/>
    <path d="M0 19Q200 64 480 74" fill="none" stroke="var(--ink-line)" stroke-width="1.4"/>
  </svg>
  <div class="footer">
    <div><svg viewBox="0 0 10 10"><circle cx="5" cy="5" r="4.3" fill="none" stroke="#fff" stroke-width=".9"/><path d="M.7 5h8.6M5 .7c-2.4 2.6-2.4 6 0 8.6M5 .7c2.4 2.6 2.4 6 0 8.6" fill="none" stroke="#fff" stroke-width=".8"/></svg>www.harrowmereprocess.com</div>
    <div><svg viewBox="0 0 10 10"><path d="M2 .8l1.8 2.3-1 1.2c.6 1.3 1.6 2.3 2.9 2.9l1.2-1L9.2 8 8 9.3C4.3 9 1 5.7.7 2Z" fill="#fff"/></svg>+1 555 014 2290<span class="sep">|</span><svg viewBox="0 0 10 10"><rect x=".5" y="2" width="9" height="6.5" fill="#fff"/><path d="M.5 2.3 5 5.8l4.5-3.5" fill="none" stroke="var(--blue-band)" stroke-width=".9"/></svg>hello@harrowmereprocess.com</div>
  </div>
</section>

</body>
</html>
```